NZ First of it's kind solutions directory and marketplace for busy Mums needs a business card design

We need a business card design for our new nationwide business in NZ (long term plans to go global). We provide solutions to the everyday challenges that busy Mums face by connecting them with quality communities and suppliers of carefully selected, relevant products and services. We sell direct via our online marketplace. The final design should communicate our values of inclusivity, quality and smart solutions. Colours should incorporate our logo colour palette of #477077 and #6ba8b2. Our website is at https://www.brightnestmums.example

Target Market(s)

busy Mums, Age 28 – 50, female, income over $100K, location main centres NZ primarily but NZ wide. Is likely juggling work or career with a young family. Probably had hobbies which have fallen by the wayside.
-Wants to succeed in her chosen career without compromising on family life
-to successfully juggle her career without feeling like she is compromising her children
- Is time poor, something always has to give and it’s generally her health (she’ll stay up late, get stressed)
- probably ex corporate or professional career. Has discretional income

Industry/Entity Type

Business

Contact Information for Business Card

Lena Forbisher, Founder, BrightNestMums.example (Strapline Tap; Gather; Sorted), 47 Kowhai Terrace, Ellerslie, Auckland 1051, New Zealand. Mob: 021 483 517 Ph: +64 (0)9 571 4860

Font styles to use
Other font styles liked:
• Raleway, and/or Architects Daughter

Colors
00a990
33b8a4
86cfc6
cfeae6

Requirements
Must have
• the above details, streamline. the logo and colours associated with those logos
Should not have
• foil or metallic colours

```html
<!DOCTYPE html>
<html lang="en">
<head>
<meta charset="utf-8">
<title>BrightNestMums business card</title>
<link rel="stylesheet" href="https://fonts.googleapis.com/css2?family=Raleway:wght@400;500;700;800&display=swap">
<style>
  :root {
    --brand-green: #00a990;
    --brand-dark: #477077;
    --brand-mid: #6ba8b2;
    --mint-soft: #cfeae6;
    --paper: #ffffff;
    --backdrop: #e4e6e6;
  }
  html, body {
    margin: 0;
    padding: 0;
    width: 1200px;
    height: 1000px;
    overflow: hidden;
    background: var(--backdrop);
    font-family: "Raleway", sans-serif;
  }
  .canvas { position: relative; width: 1200px; height: 1000px; }

  .card {
    position: absolute;
    width: 630px;
    height: 362px;
    border-radius: 38px;
    overflow: hidden;
  }

  /* front */
  .card-front { left: 150px; top: 100px; background: var(--brand-green); }
  .front-brand {
    position: absolute;
    left: 0; right: 0; top: 150px;
    display: flex;
    justify-content: center;
    align-items: center;
    gap: 16px;
  }
  .brand-dot {
    width: 40px; height: 40px;
    border-radius: 50%;
    background: var(--mint-soft);
  }
  .front-brand .brand-name {
    font-weight: 800;
    font-size: 44px;
    color: var(--paper);
    letter-spacing: -0.5px;
  }

  /* back */
  .card-back { left: 372px; top: 548px; background: var(--paper); }
  .person {
    position: absolute;
    left: 47px; top: 72px;
    color: var(--brand-green);
  }
  .person-name { font-size: 28px; font-weight: 400; margin: 0; line-height: 1; }
  .person-role { font-size: 19px; font-weight: 500; margin: 14px 0 0; line-height: 1; }

  .back-brand {
    position: absolute;
    right: 38px; top: 86px;
    display: flex; align-items: center; gap: 9px;
  }
  .back-brand .brand-dot { width: 28px; height: 28px; background: var(--brand-dark); }
  .back-brand .brand-name {
    font-weight: 800; font-size: 27px; color: var(--brand-dark); letter-spacing: -0.4px;
  }

  .contact-band {
    position: absolute;
    left: 0; right: 0; top: 174px; bottom: 0;
    background: var(--brand-green);
  }
  .address-tab { position: absolute; left: 0; top: 0; }
  .address {
    position: absolute;
    right: 31px; top: 5px;
    margin: 0;
    font-size: 17px; font-weight: 500;
    color: var(--brand-green);
  }
  .contact-list {
    list-style: none;
    margin: 0; padding: 0;
    position: absolute; left: 46px; top: 52px;
    color: var(--paper);
  }
  .contact-list li {
    display: flex; align-items: center;
    height: 35px;
    font-size: 19px; font-weight: 500;
  }
  .contact-icon { width: 24px; height: 24px; margin-right: 14px; flex: none; }
  .strapline { font-size: 14px; margin-left: 6px; }
</style>
</head>
<body>
<div class="canvas">

  <section class="card card-front" aria-label="Card front">
    <div class="front-brand">
      <span class="brand-dot"></span>
      <span class="brand-name">BrightNestMums</span>
    </div>
  </section>

  <section class="card card-back" aria-label="Card back">
    <div class="person">
      <p class="person-name">Lena Forbisher</p>
      <p class="person-role">Founder</p>
    </div>
    <div class="back-brand">
      <span class="brand-dot"></span>
      <span class="brand-name">BrightNestMums</span>
    </div>

    <div class="contact-band">
      <svg class="address-tab" width="630" height="28" viewBox="0 0 630 28" aria-hidden="true">
        <path d="M108 2 H630 V26 H126 Q116 26 113 16 Z" fill="#ffffff"/>
      </svg>
      <p class="address">47 Kowhai Terrace, Ellerslie, Auckland 1051, New Zealand</p>

      <ul class="contact-list">
        <li>
          <svg class="contact-icon" viewBox="0 0 24 24" aria-hidden="true">
            <path d="M2 8 Q2 4 12 4 Q22 4 22 8 V10 H17 V7.5 H7 V10 H2 Z" fill="#fff"/>
            <path d="M5 11 H19 L21 21 H3 Z" fill="#fff"/>
            <circle cx="12" cy="15.5" r="3.2" fill="none" stroke="#00a990" stroke-width="1.4"/>
          </svg>
          <span style="margin-left:4px">+64 (0)9 571 4860</span>
        </li>
        <li>
          <svg class="contact-icon" viewBox="0 0 24 24" aria-hidden="true">
            <path d="M6.5 3 L9.5 7.5 L7.8 9.6 Q9.5 13.5 13.6 15.6 L15.5 13.8 L20 16.8 L18.3 20 Q10 20.5 4.2 11 Q3 7 6.5 3 Z" fill="#fff"/>
          </svg>
          <span>021 483 517</span>
        </li>
        <li>
          <svg class="contact-icon" viewBox="0 0 24 24" aria-hidden="true" fill="none" stroke="#fff" stroke-width="1.8">
            <circle cx="12" cy="12" r="9.5"/>
            <ellipse cx="12" cy="12" rx="4" ry="9.5"/>
            <line x1="2.5" y1="12" x2="21.5" y2="12"/>
            <line x1="4" y1="7" x2="20" y2="7"/>
            <line x1="4" y1="17" x2="20" y2="17"/>
          </svg>
          <span>www.brightnestmums.example</span>
          <span class="strapline">( Strapline Tap; Gather; Sorted )</span>
        </li>
      </ul>
    </div>
  </section>

</div>
</body>
</html>
```